U.S. Popcorn company needs business cards

We are a popcorn company that manufactures popcorn and sells it to grocery stores worldwide. Our theme is "Americana" and our logo is U.S. route 66 which is the most famous highway in the U.S.

We would like the design to be simple and to use both sides. On the back side we would like to see just the logo and website. The front would be normal details

Target Market(s)

Wholesalers, grocers and distributors

Industry/Entity Type

Manufacture

Contact Information for Business Card

Business name: Prairie Lantern Popcorn
Phone: +1 555 308 4726
Email: Dale@prairielanternpopcorn.com
website: www.prairielanternpopcorn.com
Tag Line: "Fresh from the open road"
Name: Dale Whitcombe
Title: Founder/President

Requirements
Must have
• Either this design should be fun or clean and simple. I will let you show me your thougths.
Nice to have
• Anything that ties in the real Hwy Route 66.
• Colors might need to be red, white and blue incorporated.
Should not have
• Not be too busy.

```html
<!DOCTYPE html>
<html lang="en">
<head>
<meta charset="utf-8">
<title>Prairie Lantern Popcorn – Business Cards</title>
<link rel="stylesheet" href="https://fonts.googleapis.com/css2?family=Mulish:wght@400;600;800&display=swap">
<style>
  :root {
    --navy: #13306b;
    --red: #d8201f;
    --paper: #ffffff;
    --backdrop: #e6e6e6;
    --text: #1d2f5e;
  }
  * { margin: 0; padding: 0; box-sizing: border-box; }
  html, body {
    width: 1200px; height: 576px; overflow: hidden;
    background: var(--backdrop);
    font-family: "Mulish", "Century Gothic", sans-serif;
    color: var(--text);
  }
  .sheet { position: relative; width: 1200px; height: 576px; }
  .card {
    position: absolute; top: 139px;
    width: 484px; height: 292px;
    background: var(--paper);
    border-radius: 6px;
    overflow: hidden;
  }
  .card--back { left: 82px; }
  .card--front { left: 602px; width: 480px; }

  .brand {
    position: absolute;
    display: flex; flex-direction: column; align-items: center; justify-content: center;
    gap: 10px;
    text-align: center;
  }
  .brand__dot { width: 22px; height: 22px; border-radius: 50%; background: var(--red); }
  .brand__name {
    font-weight: 800; color: var(--navy);
    text-transform: uppercase; line-height: 1.12; letter-spacing: 0.5px;
  }
  .card--back .brand { left: 142px; top: 44px; width: 200px; height: 160px; }
  .card--back .brand__name { font-size: 24px; }
  .card--front .brand { left: 22px; top: 96px; width: 168px; height: 120px; }
  .card--front .brand__name { font-size: 20px; }

  .back-web {
    position: absolute; left: 0; right: 0; top: 256px;
    display: flex; align-items: center; justify-content: center; gap: 12px;
    font-size: 11px; font-weight: 800; color: var(--navy);
  }
  .back-web__rule { width: 52px; height: 2px; background: var(--navy); border-radius: 1px; }
  .accent { color: var(--red); }

  .header-band {
    position: absolute; left: 0; top: 0; width: 100%; height: 68px;
    background: var(--navy);
  }
  .header-rule {
    position: absolute; left: 0; top: 74px; width: 100%; height: 4px;
    background: var(--red);
  }

  .person { position: absolute; right: 24px; top: 14px; text-align: right; color: #fff; }
  .person__name { font-size: 21px; font-weight: 800; line-height: 1.2; }
  .person__title { font-size: 11px; font-weight: 400; }

  .tagline {
    position: absolute; left: 22px; top: 246px;
    font-size: 14px; font-style: normal; color: var(--navy);
  }

  .contacts {
    position: absolute; right: 22px; top: 212px;
    list-style: none; text-align: right;
    font-size: 13px; line-height: 17px; color: var(--navy);
  }
  .contacts li { display: flex; align-items: center; justify-content: flex-end; gap: 5px; }
  .contacts svg { width: 11px; height: 11px; fill: var(--red); flex: none; }
</style>
</head>
<body>
<main class="sheet">

  <section class="card card--back" aria-label="Card back">
    <div class="brand">
      <span class="brand__dot"></span>
      <span class="brand__name">Prairie Lantern<br>Popcorn</span>
    </div>
    <p class="back-web">
      <span class="back-web__rule"></span>
      <span>www.<span class="accent">prairielanternpopcorn</span>.com</span>
      <span class="back-web__rule"></span>
    </p>
  </section>

  <section class="card card--front" aria-label="Card front">
    <div class="header-band"></div>
    <div class="header-rule"></div>

    <div class="person">
      <p class="person__name">Dale Whitcombe</p>
      <p class="person__title">Founder/President</p>
    </div>

    <div class="brand">
      <span class="brand__dot"></span>
      <span class="brand__name">Prairie Lantern<br>Popcorn</span>
    </div>

    <p class="tagline">Fresh from the open road</p>

    <ul class="contacts">
      <li><span>+1 555 308 4726</span>
        <svg viewBox="0 0 24 24" aria-hidden="true"><path d="M6.6 10.8a15.1 15.1 0 0 0 6.6 6.6l2.2-2.2c.3-.3.7-.4 1-.2 1.1.4 2.3.6 3.6.6.6 0 1 .4 1 1V20c0 .6-.4 1-1 1A17 17 0 0 1 3 4c0-.6.4-1 1-1h3.5c.6 0 1 .4 1 1 0 1.3.2 2.5.6 3.6.1.3 0 .7-.2 1z"/></svg>
      </li>
      <li><span>Dale@prairielanternpopcorn.com</span>
        <svg viewBox="0 0 24 24" aria-hidden="true"><path d="M2 5h20v14H2z M2 5l10 8 10-8" stroke="#fff" stroke-width="1.5"/></svg>
      </li>
      <li><span>www.<span class="accent">prairielanternpopcorn</span>.com</span>
        <svg viewBox="0 0 24 24" aria-hidden="true"><circle cx="12" cy="12" r="10"/><path d="M2 12h20M12 2c3 3 3 17 0 20M12 2c-3 3-3 17 0 20" fill="none" stroke="#fff" stroke-width="1.4"/></svg>
      </li>
    </ul>
  </section>

</main>
</body>
</html>
```